Business Card Design For A Cajun Seafood Restaurant

We are opening a cajun seafood restaurant in a week. We mainly serve cajun seafood which is orginally from Louisiana. We want design on both sides of a business card. I have menu on the website. You can go to www.reednkettle.example to check out our menu.

Restaurant name: Reed N' Kettle
Phone: +1 (555) 304-7712
Address: 48206 Ludlow Row, #7, Bexmoor Flats, Ca90000
Email: reednkettle@mailbox.example
Website: www.reednkettle.example

Maybe add social media icons (facebook, instagram) if looks nice on the business card.
facebook.com/reednkettle
instagram.com/reednkettle or @reednkettle

Attached is the logo and other business card samples that I like.

```html
<!DOCTYPE html>
<html lang="en">
<head>
<meta charset="utf-8">
<title>Reed N' Kettle – Business Cards</title>
<link href="https://fonts.googleapis.com/css2?family=Open+Sans:wght@400;600&display=swap" rel="stylesheet">
<style>
  :root {
    --backdrop: #6f6f6f;
    --card: #ffffff;
    --orange: #f47a20;
    --orange-soft: #f9a35c;
    --orange-deep: #e0641a;
    --corn: #f5cf5a;
    --ink: #2b2b2b;
    --muted: #6a6a6a;
  }
  * { margin: 0; padding: 0; box-sizing: border-box; }
  html, body { width: 1200px; height: 950px; overflow: hidden; }
  body {
    background: radial-gradient(circle at 50% 40%, #8a8a8a, var(--backdrop));
    font-family: "Open Sans", Arial, sans-serif;
    position: relative;
  }
  .card {
    position: absolute;
    left: 230px;
    width: 740px;
    height: 423px;
    background: var(--card);
    box-shadow: 0 10px 30px rgba(0,0,0,.35);
  }
  .card--front { top: 40px; }
  .card--back { top: 487px; }

  /* Front */
  .brand {
    position: absolute;
    left: 0; right: 0; top: 150px;
    display: flex; align-items: center; justify-content: center; gap: 16px;
  }
  .brand__dot {
    width: 54px; height: 54px; border-radius: 50%;
    background: var(--orange);
  }
  .brand__name {
    font-size: 44px; font-weight: 600; color: var(--ink);
  }
  .socials {
    position: absolute; left: 0; right: 0; top: 322px;
    display: flex; justify-content: center; gap: 22px;
    font-size: 17px; color: var(--ink);
  }
  .socials__item { display: flex; align-items: center; gap: 7px; }
  .socials__mark {
    width: 18px; height: 18px; border-radius: 50%; background: var(--orange);
  }

  /* Back */
  .mascot {
    position: absolute; left: 48px; top: 56px;
    width: 350px; height: 330px;
    border-radius: 28px;
    background:
      radial-gradient(ellipse 40% 34% at 38% 32%, var(--corn), rgba(245,207,90,0) 100%),
      linear-gradient(150deg, var(--orange-soft) 0%, var(--orange) 55%, var(--orange-deep) 100%);
  }
  .person {
    position: absolute; left: 470px; top: 42px;
  }
  .person__name {
    font-size: 31px; font-weight: 400; color: var(--orange);
    text-transform: uppercase; line-height: 1.1;
  }
  .person__role { font-size: 24px; color: var(--ink); line-height: 1.3; }
  .contact {
    position: absolute; left: 470px; top: 238px;
    font-size: 16px; color: var(--muted); line-height: 1.55;
    list-style: none;
  }
  .contact__line { display: flex; align-items: center; gap: 8px; }
  .contact__icon { width: 14px; height: 14px; flex: none; fill: var(--orange); }
</style>
</head>
<body>

<section class="card card--front">
  <div class="brand">
    <span class="brand__dot"></span>
    <span class="brand__name">Reed N' Kettle</span>
  </div>
  <div class="socials">
    <span class="socials__item"><span class="socials__mark"></span>reednkettle</span>
    <span class="socials__item"><span class="socials__mark"></span>@reednkettle</span>
  </div>
</section>

<section class="card card--back">
  <div class="mascot" role="img" aria-label="Illustration of a cheerful orange crab mascot holding up an ear of corn"></div>

  <div class="person">
    <p class="person__name">Alden Marsh</p>
    <p class="person__role">CEO/Founder</p>
  </div>

  <ul class="contact">
    <li>48206 Ludlow Row, #7</li>
    <li>Bexmoor Flats, Ca90000</li>
    <li class="contact__line">
      <svg class="contact__icon" viewBox="0 0 24 24" aria-hidden="true"><path d="M6.6 10.8a15 15 0 0 0 6.6 6.6l2.2-2.2c.3-.3.7-.4 1-.2 1.1.4 2.3.6 3.6.6.6 0 1 .4 1 1V20c0 .6-.4 1-1 1C10.6 21 3 13.4 3 4c0-.6.4-1 1-1h3.5c.6 0 1 .4 1 1 0 1.3.2 2.5.6 3.6.1.3 0 .7-.2 1z"/></svg>
      +1 (555) 304-7712
    </li>
    <li class="contact__line">
      <svg class="contact__icon" viewBox="0 0 24 24" aria-hidden="true"><path d="M2 5h20v14H2z M2 5l10 8 10-8" stroke="#fff" stroke-width="1.6"/></svg>
      reednkettle@mailbox.example
    </li>
    <li class="contact__line">
      <svg class="contact__icon" viewBox="0 0 24 24" aria-hidden="true"><circle cx="12" cy="12" r="10"/><path d="M2 12h20M12 2c3 3 3 17 0 20M12 2c-3 3-3 17 0 20" stroke="#fff" stroke-width="1.4" fill="none"/></svg>
      www.reednkettle.example
    </li>
  </ul>
</section>

</body>
</html>
```